Hartwell Estates Business Cards

I would like a business card that includes myself and my partner.
Includes: Logo, office #, email, website, our names, our numbers and possibly the address. I would also like the logo to be embossed and the card to be horizontal.
There is a photo of our yard signs to give you an idea of the colors of our business.

Target Market(s)

Everyone in real estate market.
We are in a rural area. Our clientele are from all socioeconomic backgrounds.

Industry/Entity Type

Real Estate Agent

Contact Information for Business Card

Company Name: Hartwell Estates
Our Names, Titles & Cell #'s : Dana Pembrook-Broker (555).317.6624, Marla Pembrook-Realtor (555).609.1385
Office #: (555).240.3918
Website: hartwellestates-demo.com
Joint Email: pembrook@hartwellestates-demo.com
Office Address: 418B W. Calloway Ave.
Linden Ridge, OK. 70913

Font styles to use
Serif

Requirements
Must have
• HORIZONTAL, Logo, Myself and my partners names, Our cell #'s, our office #, our website, our email address
Nice to have
• Embossed logo, office address, our titles.

```html
<!DOCTYPE html>
<html lang="en">
<head>
<meta charset="utf-8">
<title>Hartwell Estates Business Cards</title>
<link href="https://fonts.googleapis.com/css2?family=Montserrat:wght@400;500;700&display=swap" rel="stylesheet">
<style>
  :root {
    --purple: #4a1170;
    --purple-emboss: #5a2685;
    --white: #ffffff;
    --ink-light: #f1eaf6;
    --backdrop: #e9e8ec;
  }
  * { margin: 0; padding: 0; box-sizing: border-box; }
  html, body { width: 1200px; height: 900px; overflow: hidden; }
  body {
    background: var(--backdrop);
    font-family: "Montserrat", sans-serif;
    position: relative;
  }
  .card {
    position: absolute;
    width: 600px;
    height: 343px;
    border-radius: 22px;
    overflow: hidden;
    box-shadow: 0 10px 28px rgba(0,0,0,0.18);
  }
  /* Back of card */
  .card-back {
    left: 300px;
    top: 70px;
    background: var(--purple);
  }
  .card-back .emboss-name {
    position: absolute;
    top: 125px;
    width: 100%;
    text-align: center;
    font-weight: 700;
    font-size: 40px;
    color: var(--purple-emboss);
    letter-spacing: 1px;
  }
  .card-back .site {
    position: absolute;
    bottom: 42px;
    width: 100%;
    text-align: center;
    font-size: 17px;
    color: var(--white);
    letter-spacing: 0.3px;
  }
  .card-back .site b { font-weight: 700; }

  /* Front of card */
  .card-front {
    left: 300px;
    top: 490px;
    background: var(--purple);
  }
  .brand-panel {
    position: absolute;
    left: 0; top: 0;
    width: 262px; height: 100%;
    background: var(--white);
  }
  .divider {
    position: absolute;
    left: 272px; top: 0;
    width: 3px; height: 100%;
    background: var(--white);
  }
  .brand {
    position: absolute;
    left: 30px;
    top: 155px;
    display: flex;
    align-items: center;
    gap: 10px;
  }
  .brand-mark {
    width: 14px; height: 14px;
    background: var(--purple);
  }
  .brand-name {
    font-weight: 700;
    font-size: 22px;
    color: var(--purple);
    letter-spacing: 0.5px;
  }
  .contacts {
    position: absolute;
    left: 296px;
    top: 36px;
    right: 18px;
    color: var(--white);
  }
  .person { margin-bottom: 10px; }
  .person-name { font-weight: 700; font-size: 21px; line-height: 1.15; }
  .person-title { font-size: 13px; line-height: 1.3; color: var(--ink-light); }
  .person-phone { font-size: 14px; line-height: 1.3; }
  .address { font-size: 14px; line-height: 1.35; margin: 4px 0 10px; }
  .contact-row {
    display: flex;
    align-items: center;
    gap: 8px;
    font-size: 13.5px;
    line-height: 1.5;
    white-space: nowrap;
  }
  .contact-row svg { width: 12px; height: 12px; flex: none; }
  .contact-row b { font-weight: 700; }
</style>
</head>
<body>

  <section class="card card-back">
    <div class="emboss-name">Hartwell Estates</div>
    <div class="site">www.<b>hartwellestates-demo</b>.com</div>
  </section>

  <section class="card card-front">
    <div class="brand-panel">
      <div class="brand">
        <span class="brand-mark"></span>
        <span class="brand-name">Hartwell Estates</span>
      </div>
    </div>
    <div class="divider"></div>

    <div class="contacts">
      <div class="person">
        <div class="person-name">Dana Pembrook</div>
        <div class="person-title">Broker</div>
        <div class="person-phone">(555).317.6624</div>
      </div>
      <div class="person">
        <div class="person-name">Marla Pembrook</div>
        <div class="person-title">Realtor</div>
        <div class="person-phone">(555).609.1385</div>
      </div>
      <div class="address">418B W. Calloway Ave.<br>Linden Ridge, OK. 70913</div>

      <div class="contact-row">
        <svg viewBox="0 0 12 12" aria-hidden="true"><path d="M2.5 1 L4.5 1 L5.2 3.5 L4 4.5 Q5 6.8 7.5 8 L8.5 6.8 L11 7.5 L11 9.5 Q10.5 11 9 11 Q1 10 1 2.5 Q1 1 2.5 1 Z" fill="#fff"/></svg>
        <span>(555).240.3918</span>
      </div>
      <div class="contact-row">
        <svg viewBox="0 0 12 12" aria-hidden="true"><rect x="0.8" y="2.3" width="10.4" height="7.4" fill="none" stroke="#fff" stroke-width="1.2"/><path d="M1 2.6 L6 6.6 L11 2.6" fill="none" stroke="#fff" stroke-width="1.2"/></svg>
        <span>pembrook@hartwellestates-demo.com</span>
      </div>
      <div class="contact-row">
        <svg viewBox="0 0 12 12" aria-hidden="true"><circle cx="6" cy="6" r="5" fill="none" stroke="#fff" stroke-width="1.1"/><ellipse cx="6" cy="6" rx="2.2" ry="5" fill="none" stroke="#fff" stroke-width="1"/><line x1="1" y1="6" x2="11" y2="6" stroke="#fff" stroke-width="1"/></svg>
        <span>www.<b>hartwellestates-demo</b>.com</span>
      </div>
    </div>
  </section>

</body>
</html>
```